Professional Baby Bottle Bank Print Design

We need a baby bottle design that is 4.25" wide x 2.28" tall with a maximum of 6 colors (white is counted as a color).

The bottle design needs to be fun but professional. Bottles with cartoon images on it will be rejected immediately.

The bottle design wraps around the bottle. See examples here: https://vel.quin/cat/BabyBottles/HarlowBottles/5

Minimum font size is 10pt.

The bottle design must have the following text on it:
Main Text: Love them both
Paragraph text: Our ministry’s aim is to not only save unborn babies, but to provide love, support, and life-saving resources for vulnerable women in our community. By filling this bottle with cash, checks, and spare coins and returning it on collection day, you are truly saving and changing lives!
Optional text: Thank you!

We are including an example file and a template file. You do NOT have to use the template - but your file has to be the exact size mentioned. If you don't design as well as our sample, please don't waste our time by spamming us with hundreds of designs. We will ban design houses that spam us with designs that are more layouts (and not well designed).

Please note - white is a color. You don't have to do a box - but anything you don't make white will be see-through.

We will take the winners of this contest to a survey with the customers. We may choose two and edit the text of one slightly to be different. We must know the fonts used.

No gradients unless they are half-toned with relatively big sized dots.

Target Market(s)

Church Attendees coming from a Pregnancy Center

Industry/Entity Type

Religious Christian Churches

Requirements
Must have
• Professional, great palette, wording as described.
Nice to have
• Integrated design across the whole space with areas for text (no text all the way across)
Should not have
• Cartoon figures; elements shoved together that don't go together (i.e. - actually design something)

```html
<!DOCTYPE html>
<html lang="en">
<head>
<meta charset="utf-8">
<title>Love Them Both – Baby Bottle Label</title>
<link rel="stylesheet" href="https://fonts.googleapis.com/css2?family=Abril+Fatface&family=PT+Sans+Narrow&display=swap">
<style>
  :root {
    --backdrop: #e6e6e6;
    --label-bg: #f6f4f8;
    --label-edge: #d9d9de;
    --love-pink: #e4416a;
    --both-blue: #1fa3dc;
    --thanks-teal: #14898c;
    --body-gray: #4f4f55;
    --skin-light: #f2c9b8;
    --skin-mid: #e4ad9a;
    --sleeve-pink: #f3cfd9;
    --star-blue: #bfe3f6;
    --star-yellow: #f8e3a6;
    --star-pink: #f4bcd0;
    --blossom: #f7d3df;
  }
  html, body {
    margin: 0;
    width: 1200px;
    height: 800px;
    overflow: hidden;
    background: var(--backdrop);
  }
  .label {
    position: absolute;
    left: 50px;
    top: 101px;
    width: 1100px;
    height: 597px;
    background: var(--label-bg);
    outline: 1px solid var(--label-edge);
    overflow: hidden;
  }
  .hands-photo {
    position: absolute;
    left: 0;
    top: 0;
    width: 440px;
    height: 100%;
    background:
      radial-gradient(ellipse 160px 220px at 280px 360px, var(--skin-mid), transparent 75%),
      radial-gradient(ellipse 120px 200px at 330px 170px, var(--skin-light), transparent 80%),
      radial-gradient(ellipse 110px 120px at 60px 250px, var(--sleeve-pink), transparent 80%),
      linear-gradient(90deg, #ece7eb 0%, #efeaee 70%, rgba(246,244,248,0) 100%);
  }
  .decor {
    position: absolute;
    border-radius: 50%;
  }
  .decor--star-blue { left: 920px; top: 40px; width: 115px; height: 110px; background: var(--star-blue); }
  .decor--star-yellow { left: 915px; top: 445px; width: 70px; height: 68px; background: var(--star-yellow); }
  .decor--star-pink { left: 38px; top: 455px; width: 84px; height: 82px; background: var(--star-pink); }
  .decor--blossom-a { left: 370px; top: 83px; width: 44px; height: 44px; background: var(--blossom); }
  .decor--blossom-b { left: 36px; top: 38px; width: 30px; height: 30px; background: var(--blossom); }
  .decor--blossom-c { left: 104px; top: 48px; width: 18px; height: 18px; background: var(--blossom); }

  .message {
    position: absolute;
    left: 478px;
    top: 22px;
    width: 580px;
  }
  .headline-love {
    margin: 0;
    font-family: "Abril Fatface", Georgia, serif;
    font-size: 92px;
    line-height: 1;
    color: var(--love-pink);
    letter-spacing: 1px;
  }
  .headline-both {
    margin: 2px 0 0 4px;
    font-family: "Abril Fatface", Georgia, serif;
    font-size: 56px;
    line-height: 1;
    color: var(--both-blue);
    letter-spacing: 1px;
  }
  .mission {
    margin: 34px 0 0 8px;
    font-family: "PT Sans Narrow", "Arial Narrow", sans-serif;
    font-size: 26.5px;
    line-height: 38px;
    color: var(--body-gray);
    text-indent: 16px;
  }
  .thanks {
    margin: 22px 0 0 0;
    font-family: "Abril Fatface", Georgia, serif;
    font-size: 42px;
    line-height: 1;
    color: var(--thanks-teal);
    letter-spacing: 1px;
  }
</style>
</head>
<body>
  <main class="label">
    <div class="hands-photo" role="img" aria-label="Photo of a mother's hand holding a newborn baby's tiny hand on a soft pink blanket"></div>
    <div class="decor decor--blossom-b" role="img" aria-label="Small pink blossom"></div>
    <div class="decor decor--blossom-c" role="img" aria-label="Small pink blossom"></div>
    <div class="decor decor--blossom-a" role="img" aria-label="Pink blossom"></div>
    <div class="decor decor--star-blue" role="img" aria-label="Pale blue star balloon"></div>
    <div class="decor decor--star-yellow" role="img" aria-label="Pale yellow star balloon"></div>
    <div class="decor decor--star-pink" role="img" aria-label="Pale pink star"></div>

    <section class="message">
      <h1 class="headline-love">Love</h1>
      <h2 class="headline-both">them both</h2>
      <p class="mission">Our ministry’s aim is to not only save unborn babies, but to provide love, support, and life-saving resources for vulnerable women in our community. By filling this bottle with cash, checks, and spare coins and returning it on collection day, you are truly saving and changing lives!</p>
      <p class="thanks">Thank you!</p>
    </section>
  </main>
</body>
</html>
```